Business Card Design for Training Business

Clear Path Coaching is a new business that delivers training and other services with a focus on topics related to mental health and wellbeing, for example, Wellmind Response Course, Resilience etc. We have a strong focus on evidence-based psychology and neuroscience. I have a logo which I will upload with the brief, so please consider colours that work well with the logo.
Target Market(s)
Adults, workplaces (particularly government and not-for-profits)
Industry/Entity Type
Business
Contact Information for Business Card
Head Strong TrainingSamantha SellwoodDirector0438 770 850sam@headstrongtraining.com.auwww.headstrongtraining.com.au

```html
<!DOCTYPE html>
<html lang="en">
<head>
<meta charset="utf-8">
<title>Clear Path Coaching – Business Card</title>
<link rel="stylesheet" href="https://fonts.googleapis.com/css2?family=Questrial&display=swap">
<style>
  :root {
    --backdrop: #3a3a3a;
    --teal: #22b8bd;
    --teal-dark: #1ba9ae;
    --card-white: #f7f7f7;
    --divider-grey: #9a9a9a;
    --ink-grey: #666666;
    --ink-white: #ffffff;
    --pattern-tint: #e4f3f3;
  }
  * { margin: 0; padding: 0; box-sizing: border-box; }
  html, body {
    width: 1200px;
    height: 750px;
    overflow: hidden;
    background: var(--backdrop);
    font-family: "Questrial", "Century Gothic", sans-serif;
  }
  .canvas {
    position: relative;
    width: 1200px;
    height: 750px;
  }
  .card {
    position: absolute;
    left: 371px;
    width: 461px;
    height: 262px;
    border-radius: 11px;
    overflow: hidden;
    background: var(--card-white);
  }
  .card--front { top: 106px; }
  .card--back { top: 388px; }
  .card svg { display: block; }
</style>
</head>
<body>
<main class="canvas">

  <section class="card card--front" aria-label="Business card front">
    <svg width="461" height="262" viewBox="0 0 461 262">
      <defs>
        <radialGradient id="pattern-glow" cx="0.55" cy="0.5" r="0.6">
          <stop offset="0" stop-color="var(--card-white)"/>
          <stop offset="1" stop-color="var(--pattern-tint)"/>
        </radialGradient>
      </defs>
      <rect class="front-panel" x="0" y="0" width="461" height="262" fill="var(--teal)"/>
      <circle class="brand-disc" cx="379" cy="131" r="145" fill="url(#pattern-glow)"
              role="img" aria-label="Faint decorative line pattern behind the brand name"/>
      <circle class="brand-disc-edge" cx="379" cy="131" r="145" fill="none"
              stroke="var(--divider-grey)" stroke-width="3"/>

      <g class="contact" fill="var(--ink-white)">
        <text class="contact-name" x="27" y="103" font-size="19">Rebecca Tanfield</text>
        <text class="contact-role" x="27" y="121" font-size="13.5">Director</text>
        <text class="contact-line" x="27" y="148" font-size="12">0491 362 517</text>
        <text class="contact-line" x="27" y="166" font-size="12">bec@clearpathcoaching.example.au</text>
        <text class="contact-line" x="27" y="184" font-size="12">www.clearpathcoaching.example.au</text>
      </g>

      <g class="brand">
        <circle class="brand-dot" cx="356" cy="110" r="30" fill="none"
                stroke="var(--teal)" stroke-width="1.5"/>
        <text class="brand-name" x="357" y="170" font-size="12" letter-spacing="1.6"
              text-anchor="middle" fill="var(--ink-grey)">CLEAR PATH COACHING</text>
      </g>
    </svg>
  </section>

  <section class="card card--back" aria-label="Business card back">
    <svg width="461" height="262" viewBox="0 0 461 262">
      <rect x="0" y="0" width="461" height="262" fill="var(--card-white)"/>
      <circle class="brand-dot" cx="231" cy="110" r="50" fill="none"
              stroke="var(--teal)" stroke-width="1.8"/>
      <text class="brand-name" x="231" y="190" font-size="13" letter-spacing="1.8"
            text-anchor="middle" fill="var(--ink-grey)">CLEAR PATH COACHING</text>
      <text class="back-web" x="231" y="235" font-size="13"
            text-anchor="middle" fill="var(--ink-grey)">www.clearpathcoaching.example.au</text>
    </svg>
  </section>

</main>
</body>
</html>
```